Label for kQm Ranch beef tallow

I need a small label to go on a 2oz amber glass jar as well as a 4 oz. amber glass jar of moisturizer.
I prefer it to be rectangular for the 2oz jar since it's small and square for the 4oz jar.
I'd like to keep our kQm Ranch logo the same font and style, which is attached. Ten Sleep, Wyoming should be left out. The font for kQm Ranch is spartan.
The label content is as follows:
Signature Tallow
Whipped Moisturizer
Ingredients: Beef Tallow, jojoba oil, peppermint oil.
2oz. jar

Instead of a white label, I'm thinking of a tan or brown label that will blend in with the amber jar. The lettering could then be a white, cream or even rust/burgandy color. Something to give it a rich look.

Thank you!

Target Market(s)

Mainly women but men as well.

Industry/Entity Type

Ranching and online beef sales

Requirements
Must have
• kQm Ranch logo

```html
<!DOCTYPE html>
<html lang="en">
<head>
<meta charset="UTF-8">
<title>kQm Ranch – Signature Tallow Labels</title>
<link rel="stylesheet" href="https://fonts.googleapis.com/css2?family=League+Spartan:wght@300;400;600&display=swap">
<style>
  :root {
    --canvas-bg: #e7e7e7;
    --label-bg: #ffffff;
    --ink: #111111;
    --band: #111111;
    --band-text: #ffffff;
    --art-light: #f2f2f2;
    --art-dark: #9a9a9a;
  }
  * { margin: 0; padding: 0; box-sizing: border-box; }
  html, body {
    width: 1200px; height: 1200px; overflow: hidden;
    background: var(--canvas-bg);
    font-family: "League Spartan", sans-serif;
    color: var(--ink);
  }
  .canvas { position: relative; width: 1200px; height: 1200px; }

  .label {
    position: absolute;
    background: var(--label-bg);
    overflow: hidden;
  }
  .label-small { left: 110px; top: 520px; width: 450px; height: 240px; border-radius: 30px; }
  .label-large { left: 620px; top: 380px; width: 440px; height: 440px; border-radius: 26px; }

  .product-line { position: absolute; font-weight: 300; text-transform: uppercase; letter-spacing: 0.2px; white-space: nowrap; }
  .label-small .product-line { left: 24px; top: 24px; font-size: 17px; }
  .label-large .product-line { left: 0; right: 0; top: 40px; text-align: center; font-size: 30px; }

  .brand-name { position: absolute; text-align: center; font-weight: 300; line-height: 0.9; white-space: nowrap; }
  .brand-name .brand-mark { display: block; letter-spacing: -2px; }
  .brand-name .brand-word { display: block; text-transform: uppercase; }
  .label-small .brand-name { left: 200px; width: 134px; top: 34px; }
  .label-small .brand-mark { font-size: 72px; }
  .label-small .brand-word { font-size: 32px; margin-top: 8px; }
  .label-large .brand-name { left: 92px; width: 204px; top: 100px; }
  .label-large .brand-mark { font-size: 112px; }
  .label-large .brand-word { font-size: 46px; margin-top: 18px; }

  .cow-art {
    position: absolute;
    background: linear-gradient(180deg, var(--art-light) 0%, var(--art-dark) 100%);
    border-radius: 6px;
  }
  .label-small .cow-art { left: 340px; top: 12px; width: 100px; height: 164px; }
  .label-large .cow-art { left: 302px; top: 96px; width: 132px; height: 222px; }

  .ingredients { position: absolute; font-weight: 600; }
  .label-small .ingredients { left: 30px; top: 108px; font-size: 12.5px; line-height: 1.25; }
  .label-large .ingredients { left: 0; right: 0; top: 380px; text-align: center; font-size: 17px; }

  .product-band {
    position: absolute; left: 0; right: 0;
    background: var(--band); color: var(--band-text);
    text-align: center; text-transform: uppercase; font-weight: 400;
  }
  .label-small .product-band { top: 186px; height: 27px; font-size: 19px; line-height: 29px; }
  .label-large .product-band { top: 330px; height: 36px; font-size: 26px; line-height: 39px; }

  .net-weight { position: absolute; left: 0; right: 0; text-align: center; font-weight: 600; }
  .label-small .net-weight { top: 220px; font-size: 12px; }
  .label-large .net-weight { top: 414px; font-size: 15px; }
</style>
</head>
<body>
<main class="canvas">

  <section class="label label-small" aria-label="2oz jar label">
    <p class="product-line">Signature Tallow</p>
    <h2 class="brand-name"><span class="brand-mark">kQm</span><span class="brand-word">Ranch</span></h2>
    <p class="ingredients">Ingredients:<br>Beef Tallow,<br>jojoba oil,<br>peppermint oil</p>
    <div class="cow-art" role="img" aria-label="Black and white drawing of a standing dairy cow on grass"></div>
    <p class="product-band">Whipped Moisturizer</p>
    <p class="net-weight">2oz.</p>
  </section>

  <section class="label label-large" aria-label="4oz jar label">
    <p class="product-line">Signature Tallow</p>
    <h2 class="brand-name"><span class="brand-mark">kQm</span><span class="brand-word">Ranch</span></h2>
    <div class="cow-art" role="img" aria-label="Black and white drawing of a standing dairy cow on grass"></div>
    <p class="product-band">Whipped Moisturizer</p>
    <p class="ingredients">Beef Tallow, jojoba oil, peppermint oil</p>
    <p class="net-weight">4oz.</p>
  </section>

</main>
</body>
</html>
```